Veldmark Supplies Business Card

Professional business card that stand out to our potential customers. Front and back with clean modern design

Industry/Entity Type

Oil and gas

Contact Information for Business Card

Name, address, website , office phone and cell number

Requirements
Must have
• Editable files for each employee

```html
<!DOCTYPE html>
<html lang="en">
<head>
<meta charset="utf-8">
<title>Veldmark Supplies Business Card</title>
<link href="https://fonts.googleapis.com/css2?family=Roboto:wght@400;500;700&display=swap" rel="stylesheet">
<style>
  :root{
    --bg:#d9dadc;
    --card:#ffffff;
    --card-shade:#f1f2f3;
    --red:#e0232b;
    --cyan:#22a8c7;
    --ink:#3a3a3a;
    --rule:#3fb3c9;
    --mark-grey:#eef0f2;
    --photo-top:#8a9ba8;
    --photo-mid:#5e8a92;
    --photo-low:#52705a;
  }
  *{box-sizing:border-box;margin:0;padding:0}
  html,body{width:1200px;height:900px;overflow:hidden}
  body{
    background:var(--bg);
    font-family:"Roboto",Arial,sans-serif;
    display:flex;flex-direction:column;align-items:center;justify-content:center;gap:44px;
  }
  .card{
    width:640px;height:366px;border-radius:26px;overflow:hidden;position:relative;
    box-shadow:0 10px 28px rgba(0,0,0,.22);
  }
  .card--front .photo-area{
    position:absolute;inset:0;
    background:linear-gradient(180deg,var(--photo-top) 0%,var(--photo-mid) 55%,var(--photo-low) 100%);
  }
  .card--front .front-name{
    position:absolute;top:22px;right:30px;
    font-weight:700;font-size:14px;letter-spacing:.06em;text-transform:uppercase;color:var(--mark-grey);
  }
  .card--back{
    background:linear-gradient(135deg,var(--card) 0%,var(--card-shade) 55%,var(--card) 100%);
  }
  .brand{
    position:absolute;top:58px;right:48px;display:flex;align-items:center;gap:10px;
  }
  .brand__square{width:18px;height:18px;background:var(--red)}
  .brand__name{font-weight:700;font-size:22px;letter-spacing:.05em;text-transform:uppercase;color:var(--red)}
  .person{position:absolute;top:138px;right:48px;text-align:right}
  .person__name{font-weight:500;font-size:22px;color:var(--red);text-transform:uppercase;line-height:1}
  .person__role{
    display:inline-block;margin-top:2px;background:var(--cyan);color:#fff;
    font-size:16px;padding:1px 8px;
  }
  .divider{position:absolute;left:46px;right:48px;top:214px;height:1px;background:var(--rule)}
  .direct{position:absolute;top:226px;right:48px;text-align:right;color:var(--ink);font-size:16px;line-height:1.45}
  .direct__phone{display:flex;align-items:center;justify-content:flex-end;gap:8px}
  .contacts{position:absolute;left:46px;bottom:30px;list-style:none;color:var(--ink);font-size:15px;line-height:1.6}
  .contacts li{display:flex;align-items:center;gap:10px}
  .icon{width:16px;height:16px;flex:none}
</style>
</head>
<body>

<section class="card card--front">
  <div class="photo-area" role="img" aria-label="Landscape photo of mountains above a turquoise lake with a forested hill in front"></div>
  <span class="front-name">Veldmark Supplies</span>
</section>

<section class="card card--back">
  <div class="brand">
    <span class="brand__square"></span>
    <span class="brand__name">Veldmark Supplies</span>
  </div>

  <div class="person">
    <div class="person__name">Dale Harmon</div>
    <span class="person__role">Director</span>
  </div>

  <div class="divider"></div>

  <div class="direct">
    <div class="direct__phone">555-300-7412
      <svg class="icon" viewBox="0 0 16 16"><rect x="4" y="1" width="8" height="14" rx="1.5" fill="none" stroke="var(--red)" stroke-width="1.5"/><circle cx="8" cy="12.5" r=".9" fill="var(--red)"/></svg>
    </div>
    <div>415 N.Cedarline Suite 2</div>
    <div>Midrock, Tx 79011</div>
  </div>

  <ul class="contacts">
    <li>
      <svg class="icon" viewBox="0 0 16 16"><path d="M3 1.5l3 .5 1 3-1.6 1.2a8 8 0 0 0 4.4 4.4L11 9l3 1 .5 3-2 1.5C6.5 14 2 9.5 1.5 3.5z" fill="var(--red)"/></svg>
      (555)214-0387
    </li>
    <li>
      <svg class="icon" viewBox="0 0 16 16"><rect x="1" y="3" width="14" height="10" fill="var(--red)"/><path d="M1 3l7 6 7-6" fill="none" stroke="#fff" stroke-width="1.2"/></svg>
      sales@veldmarksupplies.com
    </li>
    <li>
      <svg class="icon" viewBox="0 0 16 16" fill="none" stroke="var(--red)" stroke-width="1.2"><circle cx="8" cy="8" r="6.5"/><ellipse cx="8" cy="8" rx="3" ry="6.5"/><path d="M1.5 8h13M2.5 4.8h11M2.5 11.2h11"/></svg>
      www.veldmarksupplies.com
    </li>
  </ul>
</section>

</body>
</html>
```